Business Management Fortress

Assist with enhancing a powerpoint slide by providing a few design options for consideration. I have a template but open to any creative ideas.

Internal employees and stakeholders

Business Management, Finance, Accounting

• Maintain a fortress, temple, or pyramid schema
• Scenic Background

```html
<!DOCTYPE html>
<html lang="en">
<head>
<meta charset="utf-8">
<title>Business Management Fortress</title>
<link rel="stylesheet" href="https://fonts.googleapis.com/css2?family=Oswald:wght@500;600&display=swap">
<style>
  :root {
    --navy: #0c1f5a;
    --sky-light: #7fb2dc;
    --sky-mid: #4f84ba;
    --sky-deep: #2c5688;
    --stone-light: #e6e6e6;
    --stone-mid: #c4c4c4;
    --stone-dark: #8a8a8a;
    --roof-edge: #858585;
    --panel: #e0e0e0;
    --green-hi: #8fcf4e;
    --green-lo: #3e7a1c;
    --orange-hi: #f39a4f;
    --orange-lo: #b5561a;
    --yellow-hi: #ffe43a;
    --yellow-lo: #d79a00;
    --red-hi: #ff3a2a;
    --red-lo: #b50000;
    --white: #ffffff;
  }
  * { margin: 0; padding: 0; box-sizing: border-box; }
  html, body { width: 1200px; height: 675px; overflow: hidden; background: var(--sky-deep); }
  .slide { position: relative; width: 1200px; height: 675px; overflow: hidden; }
  .scenic-backdrop {
    position: absolute; inset: 0;
    background:
      linear-gradient(180deg, rgba(255,255,255,0.05) 0%, rgba(20,50,90,0.35) 100%),
      linear-gradient(110deg, var(--sky-light) 0%, var(--sky-mid) 45%, var(--sky-deep) 100%);
  }
  .temple { position: absolute; inset: 0; }
  .temple text { font-family: "Oswald", "Arial Narrow", sans-serif; }
  .roof-label { fill: var(--navy); font-weight: 600; font-size: 23px; text-anchor: middle; }
  .pillar-label { fill: var(--white); font-weight: 600; font-size: 17px; text-anchor: middle; letter-spacing: 0.5px; }
  .foundation-title { fill: var(--navy); font-weight: 600; font-size: 22px; text-anchor: middle; letter-spacing: -0.3px; }
  .foundation-list { fill: var(--navy); font-weight: 500; font-size: 13px; text-anchor: middle; letter-spacing: 0.3px; }
  .roof-frame { fill: var(--roof-edge); }
  .roof-panel { fill: var(--panel); }
  .pillar-icon { fill: rgba(255,255,255,0.85); }
</style>
</head>
<body>
<main class="slide">
  <div class="scenic-backdrop" role="img" aria-label="Blue-toned city skyline with a business professional in the background"></div>

  <svg class="temple" viewBox="0 0 1200 675" width="1200" height="675" role="group" aria-label="Business management temple">
    <defs>
      <linearGradient id="stone" x1="0" y1="0" x2="0" y2="1">
        <stop offset="0" stop-color="var(--stone-mid)"/>
        <stop offset="0.5" stop-color="var(--stone-light)"/>
        <stop offset="1" stop-color="var(--stone-dark)"/>
      </linearGradient>
      <linearGradient id="stone-top" x1="0" y1="0" x2="0" y2="1">
        <stop offset="0" stop-color="var(--stone-mid)"/>
        <stop offset="1" stop-color="var(--stone-light)"/>
      </linearGradient>
      <linearGradient id="pillar-green" x1="0" y1="0" x2="1" y2="0">
        <stop offset="0" stop-color="var(--green-lo)"/><stop offset="0.35" stop-color="var(--green-hi)"/><stop offset="1" stop-color="var(--green-lo)"/>
      </linearGradient>
      <linearGradient id="pillar-orange" x1="0" y1="0" x2="1" y2="0">
        <stop offset="0" stop-color="var(--orange-lo)"/><stop offset="0.35" stop-color="var(--orange-hi)"/><stop offset="1" stop-color="var(--orange-lo)"/>
      </linearGradient>
      <linearGradient id="pillar-yellow" x1="0" y1="0" x2="1" y2="0">
        <stop offset="0" stop-color="var(--yellow-lo)"/><stop offset="0.35" stop-color="var(--yellow-hi)"/><stop offset="1" stop-color="var(--yellow-lo)"/>
      </linearGradient>
      <linearGradient id="pillar-red" x1="0" y1="0" x2="1" y2="0">
        <stop offset="0" stop-color="var(--red-lo)"/><stop offset="0.35" stop-color="var(--red-hi)"/><stop offset="1" stop-color="var(--red-lo)"/>
      </linearGradient>
    </defs>

    <!-- foundation steps -->
    <g class="foundation">
      <path d="M150 567 H1050 L1073 619 H128 Z" fill="url(#stone)"/>
      <path d="M211 457 H980 L1027 516 H173 Z" fill="url(#stone-top)"/>
      <rect x="172" y="516" width="857" height="51" rx="4" fill="url(#stone)"/>
      <text class="foundation-title" x="600" y="550">FIDUCIARY RESPONSIBILITIES</text>
      <text class="foundation-list" x="600" y="601">ACCURATE FINANCIALS / INTERNAL CONTROLS / BRAND PROTECTION / COMPLIANCE / ETHICS / COST MANAGEMENT</text>
    </g>

    <!-- pillars -->
    <g class="pillar pillar--people">
      <rect x="240" y="440" width="94" height="55" rx="8" fill="url(#pillar-green)"/>
      <rect x="246" y="258" width="82" height="200" fill="url(#pillar-green)"/>
      <rect x="240" y="258" width="94" height="22" rx="6" fill="url(#pillar-green)"/>
      <rect class="pillar-icon" x="270" y="298" width="34" height="34" rx="4" role="img" aria-label="Family icon"/>
      <text class="pillar-label" transform="translate(293 376) rotate(-90)">PEOPLE</text>
    </g>
    <g class="pillar pillar--innovation">
      <rect x="448" y="440" width="94" height="55" rx="8" fill="url(#pillar-orange)"/>
      <rect x="454" y="258" width="82" height="200" fill="url(#pillar-orange)"/>
      <rect x="448" y="258" width="94" height="22" rx="6" fill="url(#pillar-orange)"/>
      <rect class="pillar-icon" x="478" y="298" width="34" height="34" rx="4" role="img" aria-label="Puzzle pieces icon"/>
      <text class="pillar-label" transform="translate(501 396) rotate(-90)">INNOVATION</text>
    </g>
    <g class="pillar pillar--intelligence">
      <rect x="657" y="440" width="94" height="55" rx="8" fill="url(#pillar-yellow)"/>
      <rect x="663" y="258" width="82" height="200" fill="url(#pillar-yellow)"/>
      <rect x="657" y="258" width="94" height="22" rx="6" fill="url(#pillar-yellow)"/>
      <rect class="pillar-icon" x="687" y="298" width="34" height="34" rx="4" role="img" aria-label="Head with gears icon"/>
      <text class="pillar-label" transform="translate(710 400) rotate(-90)">INTELLIGENCE</text>
    </g>
    <g class="pillar pillar--alliances">
      <rect x="866" y="440" width="94" height="55" rx="8" fill="url(#pillar-red)"/>
      <rect x="872" y="258" width="82" height="200" fill="url(#pillar-red)"/>
      <rect x="866" y="258" width="94" height="22" rx="6" fill="url(#pillar-red)"/>
      <rect class="pillar-icon" x="896" y="298" width="34" height="34" rx="4" role="img" aria-label="Strategy board icon"/>
      <text class="pillar-label" transform="translate(910 388) rotate(-90)">STRATEGIC</text>
      <text class="pillar-label" transform="translate(928 388) rotate(-90)">ALLIANCES</text>
    </g>

    <!-- entablature -->
    <path d="M195 200 H1005 Q1012 200 1011 210 L1006 262 H194 L189 210 Q188 200 195 200 Z" fill="url(#stone)"/>

    <!-- pediment -->
    <g class="roof">
      <path class="roof-frame" d="M600 37 L998 200 H197 Z"/>
      <path class="roof-panel" d="M417 121 L586 192 H246 Z"/>
      <path class="roof-panel" d="M600 47 L778 118 L600 190 L427 118 Z"/>
      <path class="roof-panel" d="M786 123 L958 192 H619 Z"/>
      <text class="roof-label" x="600" y="130">PARTNER</text>
      <text class="roof-label" x="403" y="176">LEADER</text>
      <text class="roof-label" x="787" y="176">PROFITABILITY</text>
    </g>
  </svg>
</main>
</body>
</html>
```